Redesign Website - Current one too plain

The description is in the uploaded file. Please let me know if you need any more information. I'd prefer it if someone could implement the design to a WordPress site but the best design will win, regardless.
I would like the forms to look nice as well
UPDATE:
I don't think we can use the images that I provided, I think they make the site look a bit 'cheap' and I really don't know how to replace them. One thought I have had is to make the "Simple, Unique, Effective" a second feature on the right side of the page with the search on the left
Target Market(s)
Small companies, private sellers of cars and people who rent their caravan/holiday home out
Industry/Entity Type
Advertising
Number of Pages Required
3 page
Colors
Designer to choose colors to be used in the design.
Look and feel
Each slider illustrates characteristics of the customer's brand and the style your logo design should communicate.

```html
<!DOCTYPE html>
<html lang="en">
<head>
<meta charset="utf-8">
<title>DOTTO – Simple. Unique. Effective.</title>
<link href="https://fonts.googleapis.com/css2?family=Poppins:ital,wght@0,400;0,500;0,600;0,700;0,800;0,900;1,400&display=swap" rel="stylesheet">
<style>
:root{
  --ink:#222;
  --dark:#111111;
  --blue:#1565c9;
  --yellow:#f5d600;
  --pale-yellow:#f7fccf;
  --grey-band:#f1f1f1;
  --white:#ffffff;
  --muted:#555;
}
*{box-sizing:border-box;margin:0;padding:0}
html,body{width:1200px;height:3378px;overflow:hidden}
body{font-family:'Poppins',sans-serif;color:var(--ink);background:var(--white);position:relative}
.abs{position:absolute}
/* header */
.site-header{position:absolute;left:0;top:0;width:1200px;height:115px;background:var(--dark)}
.brand{position:absolute;left:75px;top:44px;display:flex;align-items:center;gap:10px;font-size:28px;font-weight:400;letter-spacing:3px;color:var(--yellow)}
.brand-dot{width:26px;height:26px;border-radius:50%;background:var(--yellow)}
.main-nav{position:absolute;right:75px;top:38px;display:flex;align-items:center;gap:38px}
.main-nav a{color:var(--white);font-weight:600;font-size:16px;text-decoration:none}
.main-nav a.active{color:var(--yellow)}
.main-nav a.login{border:2px solid var(--yellow);border-radius:22px;padding:7px 16px}
/* hero */
.hero{position:absolute;left:0;top:115px;width:1200px;height:675px;background:linear-gradient(110deg,#e7f0fb 0%,#f6f9fd 30%,#dfe9fa 100%)}
.hero-tag{position:absolute;left:73px;top:154px;font-size:38px;font-weight:500;color:var(--blue);word-spacing:10px;white-space:nowrap;z-index:2}
.hero-code{position:absolute;left:72px;top:200px;font-size:128px;font-weight:800;line-height:1;color:var(--dark);letter-spacing:4px}
.code-arrows{position:absolute;left:80px;top:340px;display:flex;gap:28px}
.chip-row{position:absolute;left:75px;top:415px;display:flex;gap:9px}
.chip{height:40px;padding:0 14px;border-radius:20px;background:var(--blue);color:var(--white);font-size:14px;display:flex;align-items:center}
.btn-yellow{position:absolute;background:var(--yellow);color:var(--white);font-weight:600;border-radius:32px;display:flex;align-items:center;justify-content:center}
.hero-visual{position:absolute;left:376px;top:154px;width:824px;height:466px}
.hero-visual .caravan{position:absolute;left:306px;top:0;width:470px;height:250px;border-radius:8px;background:linear-gradient(180deg,#b4b8bd 0%,#e4e4e2 40%,#c9cac8 100%)}
.hero-visual .car{position:absolute;left:0;top:144px;width:400px;height:170px;border-radius:80px 60px 30px 30px;background:linear-gradient(180deg,#a9a8a4 0%,#8c8b88 60%,#6f6f6d 100%)}
.hero-visual .van{position:absolute;left:279px;top:246px;width:545px;height:220px;border-radius:90px 40px 30px 30px;background:linear-gradient(180deg,#d8d9db 0%,#b3b5b8 60%,#8f9195 100%)}
/* features */
.feature-card{position:absolute;top:860px;width:328px;height:452px;background:var(--white);border-radius:10px;box-shadow:0 4px 18px rgba(0,0,0,.09);border-bottom:6px solid var(--yellow);text-align:center}
.feature-blob{position:absolute;left:54px;top:20px;width:220px;height:220px;border-radius:50%;background:var(--pale-yellow)}
.feature-icon{position:absolute;left:134px;top:100px}
.feature-card h3{position:absolute;top:278px;width:100%;font-size:32px;font-weight:800;color:var(--blue)}
.feature-card p{position:absolute;top:326px;width:100%;padding:0 20px;font-size:15.5px;line-height:28px;color:var(--ink)}
/* about */
.eyebrow{position:absolute;font-size:30px;font-weight:500;color:var(--blue)}
.big-title{position:absolute;font-size:100px;font-weight:900;line-height:1;color:var(--ink)}
.about-text{position:absolute;left:75px;top:1705px;width:520px;font-size:17.5px;line-height:37px;color:var(--ink)}
.about-visual{position:absolute;left:610px;top:1430px;width:517px;height:521px;border-radius:46% 54% 48% 52%/50% 44% 56% 50%;background:linear-gradient(180deg,#c9d6e4 0%,#eef0ec 45%,#7f8f6b 100%)}
/* testimonials */
.review-card{position:absolute;top:2203px;width:328px;height:276px;background:var(--white);border-radius:10px;box-shadow:0 4px 18px rgba(0,0,0,.08);padding:44px 24px 0}
.quote-mark{position:absolute;left:16px;top:8px;font-size:90px;font-weight:900;line-height:1;color:#f7ec9b}
.review-card p{position:relative;font-size:15.5px;font-style:italic;line-height:27.5px;color:var(--ink)}
.review-card h4{position:relative;margin-top:10px;font-size:17.5px;font-weight:700;color:var(--blue)}
/* contact */
.contact{position:absolute;left:0;top:2567px;width:1200px;height:608px;background:linear-gradient(160deg,#1a6ad0 0%,#1565c9 55%,#1559b8 100%)}
.field-label{position:absolute;font-size:15px;color:var(--white)}
.field-line{position:absolute;height:1px;background:rgba(255,255,255,.8)}
/* footer */
.footer-brand{position:absolute;left:75px;top:3228px;display:flex;align-items:center;gap:10px;font-size:28px;letter-spacing:3px;color:#555}
.footer-brand .brand-dot{background:#666}
.copyright{position:absolute;left:76px;top:3285px;font-size:14px;line-height:28px;color:var(--muted)}
.social{position:absolute;left:879px;top:3266px;display:flex;gap:28px}
.social span{width:28px;height:28px;border-radius:50%;background:var(--yellow)}
</style>
</head>
<body>

<header class="site-header">
  <div class="brand"><span class="brand-dot"></span>DOTTO</div>
  <nav class="main-nav">
    <a class="active" href="#">Home</a>
    <a href="#">Advertise</a>
    <a href="#">Contact</a>
    <a href="#">Register</a>
    <a class="login" href="#">Login</a>
  </nav>
</header>

<section class="hero">
  <div class="hero-visual" role="img" aria-label="Silver car, static caravan and van each showing a short code tag">
    <div class="caravan"></div>
    <div class="car"></div>
    <div class="van"></div>
  </div>
  <div class="hero-tag">Simple. Unique. Effective.</div>
  <div class="hero-code">A 1</div>
  <div class="code-arrows">
    <svg width="180" height="36" viewBox="0 0 180 36" fill="none" stroke="#111" stroke-width="3" stroke-linecap="round">
      <path d="M16 4 L4 18 L16 32"/><path d="M52 4 L64 18 L52 32"/>
      <path d="M122 4 L110 18 L122 32"/><path d="M158 4 L170 18 L158 32"/>
    </svg>
  </div>
  <div class="chip-row">
    <span class="chip" style="width:89px;justify-content:center">Car</span>
    <span class="chip">Caravan</span>
    <span class="chip">Company</span>
  </div>
  <a class="btn-yellow" style="left:75px;top:482px;width:178px;height:54px;font-size:19px;font-weight:500">Search</a>
</section>

<section class="features">
  <article class="feature-card" style="left:75px">
    <div class="feature-blob"></div>
    <svg class="feature-icon" width="60" height="80" viewBox="0 0 60 80" fill="none" stroke="#111" stroke-width="2.5" stroke-linecap="round">
      <path d="M30 4 C14 4 4 16 4 30 C4 42 14 48 16 58 L44 58 C46 48 56 42 56 30 C56 16 46 4 30 4Z"/>
      <path d="M18 64 H42 M20 70 H40 M24 76 H36"/><path d="M20 30 Q25 25 30 30 Q35 35 40 30"/>
    </svg>
    <h3>Simple</h3>
    <p>Create&nbsp; your advert and display<br>your code</p>
  </article>
  <article class="feature-card" style="left:437px">
    <div class="feature-blob"></div>
    <svg class="feature-icon" width="76" height="76" viewBox="0 0 76 76" fill="none" stroke="#111" stroke-width="2.5" stroke-linecap="round">
      <path d="M8 34 C8 18 20 6 34 6 C48 6 58 16 60 28"/><path d="M16 54 C14 46 14 40 16 34 C18 22 26 16 34 16 C42 16 48 22 50 30"/>
      <path d="M26 62 C22 52 22 42 26 34 C28 28 32 26 34 26"/><path d="M34 36 C32 46 34 56 38 64"/>
      <circle cx="50" cy="46" r="12"/><path d="M59 55 L72 70"/>
    </svg>
    <h3>Unique</h3>
    <p>Customers find you by<br>an easy-to-remember code</p>
  </article>
  <article class="feature-card" style="left:799px">
    <div class="feature-blob"></div>
    <svg class="feature-icon" width="76" height="70" viewBox="0 0 76 70" fill="none" stroke="#111" stroke-width="2.5" stroke-linejoin="round" stroke-linecap="round">
      <path d="M6 30 H22 V66 H6Z"/><path d="M22 32 L34 10 C36 4 44 6 42 14 L40 26 H60 C66 26 68 32 64 36 C68 40 66 46 62 46 C64 50 62 56 58 56 C60 60 56 66 52 64 H22"/>
      <path d="M66 40 V66 H56"/><path d="M10 4 L12 10 M4 12 L10 12"/>
    </svg>
    <h3>Effective</h3>
    <p>Customers are directed to you and<br>not a list of your competitors</p>
  </article>
</section>

<section class="about">
  <div class="eyebrow" style="left:75px;top:1421px">About Us</div>
  <div class="big-title" style="left:73px;top:1472px">Welcome</div>
  <div class="big-title" style="left:73px;top:1572px;color:var(--yellow)">DOTTO</div>
  <p class="about-text">Nemo enim ipsam voluptatem quia voluptas sit<br>aspernatur aut odit&nbsp; aut fugit, sed quia consequuntur<br>magni dolores eos qui ratione voluptatem sequi nesciunt.<br>Nam libero tempore, cum soluta nobis.</p>
  <a class="btn-yellow" style="left:75px;top:1888px;width:194px;height:62px;font-size:19px">Learn More</a>
  <div class="about-visual" role="img" aria-label="Row of static caravans on a grassy holiday park under a cloudy sky"></div>
</section>

<section class="testimonials">
  <svg class="abs" style="left:0;top:2040px" width="600" height="325" viewBox="0 0 600 325">
    <path d="M0 0 H510 Q528 0 536 18 L600 170 V325 H0Z" fill="var(--grey-band)"/>
  </svg>
  <div class="eyebrow" style="right:73px;top:2032px">Customer Review</div>
  <div class="big-title" style="right:73px;top:2076px">Testimonials</div>
  <article class="review-card" style="left:75px">
    <span class="quote-mark">“</span>
    <p>Nam libero tempore, cum soluta nobis est eligendi optio cumque nihil impedit quo minus&nbsp; debitis aut rerum necessitatibus saepe eveniet ut et voluptates repudiandae sint et molestiae non recusandae..”</p>
    <h4>Name Heading</h4>
  </article>
  <article class="review-card" style="left:437px">
    <span class="quote-mark">“</span>
    <p>Nam libero tempore, cum soluta nobis est eligendi optio cumque nihil impedit quo minus&nbsp; debitis aut rerum necessitatibus saepe eveniet ut et voluptates repudiandae sint et molestiae non recusandae..”</p>
    <h4>Name Heading</h4>
  </article>
  <article class="review-card" style="left:799px">
    <span class="quote-mark">“</span>
    <p>Nam libero tempore, cum soluta nobis est eligendi optio cumque nihil impedit quo minus&nbsp; debitis aut rerum necessitatibus saepe eveniet ut et voluptates repudiandae sint et molestiae non recusandae..”</p>
    <h4>Name Heading</h4>
  </article>
</section>

<section class="contact" role="img" aria-label="Blue-tinted motorhome parked by mountains, behind the contact form">
  <div class="eyebrow" style="left:0;width:1200px;text-align:center;top:64px;color:var(--yellow)">Get in Touch</div>
  <div class="big-title" style="left:0;width:1200px;text-align:center;top:106px;color:var(--white)">Contact Us</div>
  <span class="field-label" style="left:254px;top:252px">Name</span>
  <span class="field-label" style="left:616px;top:252px">Email</span>
  <div class="field-line" style="left:254px;top:299px;width:332px"></div>
  <div class="field-line" style="left:616px;top:299px;width:330px"></div>
  <span class="field-label" style="left:254px;top:320px">Message</span>
  <div class="field-line" style="left:254px;top:432px;width:692px"></div>
  <a class="btn-yellow" style="left:504px;top:473px;width:192px;height:62px;font-size:19px">Submit</a>
</section>

<footer>
  <div class="footer-brand"><span class="brand-dot"></span>DOTTO</div>
  <p class="copyright">© Copyright 2023 Company Name.<br>All Rights Reserved.</p>
  <div class="social">
    <span aria-label="Social link 1"></span><span aria-label="Social link 2"></span><span aria-label="Social link 3"></span><span aria-label="Social link 4"></span><span aria-label="Social link 5"></span>
  </div>
</footer>

</body>
</html>
```